Modern 6 page design, business card, and a banner

I need a website design for my CFO service. The service uses proprietary tech, so it needs to be modern. I also need business card and banner design to match the site.
The banner size is 33.75 X 79.25.
I'm open to colors and styles.

Target Market(s)

Startups

Coding

Coded - Design and coding required

Number of Pages Required

5+ page

```html
<!DOCTYPE html>
<html lang="en">
<head>
<meta charset="utf-8">
<title>Ledgra — Strategic Financial Planner</title>
<link rel="stylesheet" href="https://fonts.googleapis.com/css2?family=Quicksand:wght@500;600;700&family=Nunito:wght@400;600;700&family=Cutive+Mono&display=swap">
<style>
  :root{
    --navy:#231f44;
    --navy-soft:#2b2856;
    --blue:#2563c4;
    --blue-bright:#3b7fd8;
    --ink:#1f1c3b;
    --body:#2a2a33;
    --coral:#d9826f;
    --white:#ffffff;
    --screen:#1b3f8f;
    --device:#e9ebef;
  }
  *{margin:0;padding:0;box-sizing:border-box}
  html,body{width:1200px;height:3835px;overflow:hidden;background:var(--white)}
  body{position:relative;font-family:"Nunito",sans-serif;color:var(--body)}
  .backdrop{position:absolute;left:0;top:0;z-index:0}
  .layer{position:absolute;z-index:1}

  .burger{left:75px;top:24px;width:26px}
  .burger span{display:block;height:3px;background:var(--white);margin-bottom:5px;border-radius:2px}
  .topnav{top:30px;left:0;width:1200px;height:24px}
  .topnav a{position:absolute;font-family:"Quicksand",sans-serif;font-weight:600;font-size:16px;color:var(--white);text-decoration:none;white-space:nowrap}
  .topnav a.is-active{color:var(--blue-bright)}

  .brand{font-family:"Quicksand",sans-serif;font-weight:700;color:var(--white);line-height:1;white-space:nowrap}
  .tagline{font-family:"Cutive Mono",monospace;color:var(--coral);letter-spacing:1px;white-space:nowrap}

  .hero-title{left:76px;top:310px;font-family:"Quicksand",sans-serif;font-weight:700;font-size:46px;color:var(--white);white-space:nowrap}
  .hero-sub{left:76px;top:368px;font-family:"Quicksand",sans-serif;font-weight:600;font-size:18px;color:var(--white);white-space:nowrap}

  .device{background:var(--device);border:3px solid #d2d5dc;box-shadow:0 10px 30px rgba(0,0,0,.25)}
  .device .screen{position:absolute;background:var(--screen)}

  .heading{font-family:"Quicksand",sans-serif;font-weight:700;color:var(--ink);text-align:center;line-height:1.15}
  .heading .accent{color:var(--blue)}
  .copy{font-size:14px;color:var(--body);text-align:center}

  .btn{display:flex;align-items:center;justify-content:center;background:var(--blue);color:var(--white);font-family:"Quicksand",sans-serif;font-weight:700;font-size:16px;letter-spacing:.5px;border-radius:30px;text-decoration:none}

  .step-badge{width:66px;height:66px;border-radius:50%;background:var(--blue);border:4px solid var(--white);color:var(--white);font-family:"Quicksand",sans-serif;font-weight:500;font-size:32px;display:flex;align-items:center;justify-content:center;box-shadow:0 0 0 1px #d7dbe6}
  .step-icon{width:58px;height:58px;border-radius:8px;background:#e3e6ee}
  .step-label{width:134px;height:25px;background:var(--blue);color:var(--white);font-weight:700;font-size:14px;display:flex;align-items:center;justify-content:center}
  .step-desc{width:150px;font-size:11.5px;line-height:14.5px;text-align:center;color:#333}

  .subhead{font-family:"Nunito",sans-serif;font-weight:700;font-size:19px;color:var(--ink);text-align:center}

  .contact-title{left:724px;top:3285px;font-family:"Quicksand",sans-serif;font-weight:600;font-size:50px;color:var(--white)}
  .field{left:725px;width:401px;border-bottom:1px solid #a8a7c0}
  .field span{position:absolute;left:9px;bottom:10px;font-family:"Quicksand",sans-serif;font-weight:600;font-size:15px;color:var(--white)}
  .social{width:18px;height:18px;border-radius:50%;background:var(--white)}
  .footnav a{position:absolute;font-family:"Quicksand",sans-serif;font-weight:600;font-size:15px;color:var(--white);text-decoration:none;white-space:nowrap}
  .copyright{left:0;width:1200px;top:3788px;text-align:center;font-family:"Quicksand",sans-serif;font-weight:600;font-size:14px;color:var(--white)}
</style>
</head>
<body>

<svg class="backdrop" width="1200" height="3835" viewBox="0 0 1200 3835" aria-hidden="true">
  <path d="M1200 70 V260 C1170 460 1120 610 1000 650 C870 690 770 600 650 590 C520 580 470 700 320 690 C220 684 140 640 0 600 V560 Z" fill="var(--blue)"/>
  <path d="M0 0 H1200 V80 C1150 240 1100 520 990 585 C880 640 770 560 650 550 C520 540 460 660 320 655 C200 650 120 610 0 605 Z" fill="var(--navy)"/>
  <g stroke="var(--blue)" stroke-width="3" fill="none">
    <path d="M5 250 h30 M45 250 h30"/>
    <path d="M620 440 h22 M652 440 h22 M684 440 h22"/>
    <path d="M1128 85 h25 M1163 85 h25"/>
    <path d="M638 1993 h22 M668 1993 h16"/>
    <path d="M1088 2191 h22 M1118 2191 h22"/>
    <path d="M78 2688 h22 M108 2688 h16"/>
    <path d="M530 2880 h20 M556 2880 h20"/>
  </g>

  <path d="M700 1880 C800 1800 990 1810 1090 1880 C1190 1950 1190 2130 1150 2240 C1110 2340 1000 2380 900 2350 C800 2320 700 2290 670 2180 C640 2070 640 1930 700 1880 Z" fill="var(--blue)"/>
  <path d="M690 1870 C780 1800 960 1820 1060 1880 C1160 1940 1170 2110 1130 2220 C1090 2320 990 2360 890 2330 C790 2300 690 2270 660 2160 C630 2050 620 1920 690 1870 Z" fill="var(--navy-soft)"/>

  <path d="M150 2550 C240 2480 420 2500 520 2560 C620 2620 640 2780 610 2900 C580 3020 470 3100 360 3090 C250 3080 150 3040 110 2940 C70 2840 60 2620 150 2550 Z" fill="var(--blue)"/>
  <path d="M130 2570 C210 2500 390 2520 490 2580 C590 2640 600 2790 570 2900 C540 3010 440 3080 330 3070 C220 3060 130 3020 100 2920 C70 2820 50 2640 130 2570 Z" fill="var(--navy-soft)"/>

  <path d="M0 3330 C180 3280 330 3220 520 3220 C700 3220 760 3230 880 3180 C1020 3120 1100 3110 1200 3100 V3835 H0 Z" fill="var(--blue)"/>
  <path d="M0 3430 C170 3360 330 3290 520 3285 C700 3280 780 3280 900 3235 C1030 3185 1110 3170 1200 3165 V3835 H0 Z" fill="var(--navy)"/>
  <g stroke="var(--blue)" stroke-width="3" fill="none">
    <path d="M0 3533 h22 M28 3533 h18"/>
    <path d="M503 3615 h22 M531 3615 h18"/>
    <path d="M1155 3358 h22 M1183 3358 h18"/>
  </g>
</svg>

<div class="layer burger"><span></span><span></span><span></span></div>
<nav class="layer topnav">
  <a class="is-active" style="left:355px">Home</a>
  <a style="left:449px">How it works</a>
  <a style="left:602px">Ledgra Mobile App</a>
  <a style="left:780px">Why Ledgra Visual Finance?</a>
  <a style="left:1035px">Contact Us</a>
</nav>

<div class="layer brand" style="left:78px;top:150px;font-size:64px">Ledgra</div>
<div class="layer tagline" style="left:78px;top:270px;font-size:17px">Strategic Financial Planner</div>
<h1 class="layer hero-title">Ledgra combines hands-on</h1>
<p class="layer hero-sub">financial planning services with real-time mobile monitoring</p>

<div class="layer device" style="left:725px;top:156px;width:377px;height:517px;border-radius:22px">
  <div class="screen" role="img" aria-label="Tablet showing the Ledgra dashboard with sales, income, expenses, GP, cash and loan gauges" style="left:22px;top:48px;width:327px;height:411px"></div>
</div>

<h2 class="layer heading" style="left:0;width:1200px;top:792px;font-size:45px">Welcome <span class="accent">To Ledgra</span></h2>
<p class="layer copy" style="left:100px;width:1000px;top:884px;line-height:33px">Small businesses can visualize their finances, have a plan they trust and monitor progress daily. No more waiting for the latest monthly or quarterly report from your accountant. No more late nights digging through spreadsheets to figure out where you really stand. No more wondering if you’re prepared for the future. Ledgra delivers a clear financial plan tailored to your business goals, an easy mobile dashboard to track progress on a daily basis and all the professional advice and support you need along the way.</p>
<a class="layer btn" style="left:502px;top:1042px;width:195px;height:57px">LEARN MORE</a>

<h2 class="layer heading" style="left:0;width:1200px;top:1175px;font-size:45px">How it <span class="accent">Works</span></h2>
<p class="layer copy" style="left:140px;width:920px;top:1284px;line-height:28px">Ledgra combines traditional bookkeeping and “outsourced CFO” services with a customizable visual finance mobile app. We provide everything needed to develop a plan, clean and structure your accounting data and launch your visual finance dashboard.</p>

<svg class="layer" style="left:0;top:1400px" width="1200" height="200" aria-hidden="true">
  <g fill="none" stroke="#9a9aa6" stroke-width="1.5">
    <path d="M172 100 A89 89 0 0 1 350 100" stroke-dasharray="2 6"/><path d="M172 100 A89 89 0 0 0 350 100"/>
    <path d="M348 100 A89 89 0 0 1 526 100"/><path d="M348 100 A89 89 0 0 0 526 100" stroke-dasharray="2 6"/>
    <path d="M524 100 A89 89 0 0 1 702 100" stroke-dasharray="2 6"/><path d="M524 100 A89 89 0 0 0 702 100"/>
    <path d="M701 100 A89 89 0 0 1 879 100"/><path d="M701 100 A89 89 0 0 0 879 100" stroke-dasharray="2 6"/>
    <path d="M879 100 A89 89 0 0 1 1057 100" stroke-dasharray="2 6"/><path d="M879 100 A89 89 0 0 0 1057 100"/>
  </g>
</svg>
<div class="layer step-icon" role="img" aria-label="Computer icon" style="left:232px;top:1470px"></div>
<div class="layer step-icon" role="img" aria-label="Folder icon" style="left:408px;top:1470px"></div>
<div class="layer step-icon" role="img" aria-label="Report document icon" style="left:584px;top:1462px"></div>
<div class="layer step-icon" role="img" aria-label="Browser with magnifier icon" style="left:761px;top:1470px"></div>
<div class="layer step-icon" role="img" aria-label="Calendar with clock icon" style="left:939px;top:1465px"></div>
<div class="layer step-badge" style="left:140px;top:1444px">01</div>
<div class="layer step-badge" style="left:366px;top:1393px">02</div>
<div class="layer step-badge" style="left:551px;top:1538px">03</div>
<div class="layer step-badge" style="left:720px;top:1393px">04</div>
<div class="layer step-badge" style="left:898px;top:1544px">05</div>

<div class="layer step-label" style="left:178px;top:1617px">Develop Plan</div>
<div class="layer step-label" style="left:356px;top:1618px">Clean Data</div>
<div class="layer step-label" style="left:533px;top:1618px">Visual Finances</div>
<div class="layer step-label" style="left:709px;top:1617px">Monitor Daily</div>
<div class="layer step-label" style="left:885px;top:1617px">Advise Monthly</div>
<p class="layer step-desc" style="left:170px;top:1652px">we work with you to develop a 3 to 5 year financial plan tailored to your business goals.</p>
<p class="layer step-desc" style="left:348px;top:1652px">our bookkeepers clean your historical data, set-up live data intake, and ensure alignment with finance reports</p>
<p class="layer step-desc" style="left:522px;top:1652px">we launch your customized visual finance dashboard on Ledgra Mobile</p>
<p class="layer step-desc" style="left:701px;top:1652px">you monitor real financial results against plan on a daily basis</p>
<p class="layer step-desc" style="left:877px;top:1652px">our financial experts provide support and help respond as your business grows</p>

<h2 class="layer heading" style="left:66px;width:540px;top:1918px;font-size:45px">Ledgra <span class="accent">Mobile App</span></h2>
<p class="layer subhead" style="left:86px;width:500px;top:2015px">Visualize your finances in real time.</p>
<p class="layer copy" style="left:76px;width:520px;top:2048px;line-height:33.3px">Ledgra delivers an easy-to-understand dashboard using our own mobile app, customized for your business and your specific plan. Relying on clean data and mirroring your actual financial statements, Ledgra lets you see what a CFO sees and always be confident you’re looking at real numbers. Monitor results daily, understand where you stand versus plan and make better decisions with Ledgra Mobile.</p>
<a class="layer btn" style="left:240px;top:2277px;width:194px;height:56px">LEARN MORE</a>

<div class="layer device" style="left:770px;top:1830px;width:260px;height:539px;border-radius:34px">
  <div class="screen" role="img" aria-label="Phone showing the global sales dashboard with income, expenses, cash and loan gauges" style="left:8px;top:54px;width:238px;height:420px"></div>
</div>

<div class="layer device" style="left:214px;top:2504px;width:282px;height:611px;border-radius:36px">
  <div class="screen" role="img" aria-label="Phone showing a goals list with progress bars" style="left:8px;top:64px;width:260px;height:474px;background:#f2f3f6"></div>
</div>
<h2 class="layer heading" style="left:620px;width:510px;top:2545px;font-size:47px">Why Ledgra<br><span class="accent">Visual Finance?</span></h2>
<p class="layer copy" style="left:615px;width:520px;top:2712px;line-height:33.3px">Small businesses shouldn’t be forced to choose between the strategic value of traditional financial services and the convenience of modern mobile reporting technology. With Ledgra, you have access to decades of financial planning experience and a daily view into real finance reports - all delivered through a mobile app you can take with you on the road, in the field, on the shop floor or wherever you need to be.</p>
<a class="layer btn" style="left:776px;top:2944px;width:196px;height:56px">LEARN MORE</a>

<h2 class="layer contact-title">Contact Us</h2>
<div class="layer field" style="top:3370px;height:38px"><span>Name</span></div>
<div class="layer field" style="top:3435px;height:38px"><span>Email</span></div>
<div class="layer field" style="top:3500px;height:85px"><span style="bottom:24px">Messae</span></div>
<a class="layer btn" style="left:725px;top:3618px;width:196px;height:56px;font-size:21px;font-weight:600;letter-spacing:0">Submit</a>

<div class="layer brand" style="left:92px;top:3500px;font-size:64px">Ledgra</div>
<div class="layer tagline" style="left:92px;top:3613px;font-size:17px">Strategic Financial Planner</div>
<div class="layer social" style="left:96px;top:3663px"></div>
<div class="layer social" style="left:142px;top:3663px"></div>
<div class="layer social" style="left:188px;top:3663px;border-radius:3px"></div>

<nav class="layer footnav" style="left:0;top:3740px;width:1200px;height:22px">
  <a style="left:269px">Home</a>
  <a style="left:353px">How it works</a>
  <a style="left:489px">Ledgra Mobile App</a>
  <a style="left:646px">Why Ledgra Visual Finance?</a>
  <a style="left:874px">Contact Us</a>
</nav>
<p class="layer copyright">© 2019 &nbsp;| &nbsp;&nbsp;www.ledgra-finance.example</p>

</body>
</html>
```